Keystonery Billboard - Financial Services Company (Investments, Tax Planning and Insurance)

Our new office has a billboard directly above the office building. We'd like something eye-catching with a strong Call to Action, with the main part of the billboard being under 7 words if possible. We'd like you to include a way to get ahold of us (either our website keystoneryllc.example or our phone number 302-418-2907. You may also include in small font something to indicate that we've been serving the area since 1980 (the DE area, the tri-state area, the Marlowe Hollow, etc.)

We offer financial planning, tax planning, and insurance, and we help our clients to focus on their goals and happiness by providing everything they need for lifelong wealth under one roof.

Our logos are attached, we use a triangle logo with green and gray. We use the tagline "discover lasting prosperity" but this does not need to be included.

Potential ideas we have seen from other financial companies-
- the concept that the driver spends more time looking at billboards than planning for their retirement
-something along the lines of "everything you need for your finances is in this building right here" planning, investments, taxes, insurance"
-don't spend your time worrying about retirement, let us help you plan for it
-are you working for your money, or is it working for you?
- retirement takes planning, we're here to help
- ready to retire? talk to us
- need investment advice?
- need help investing?
- crossing your fingers isn't a retirement plan. we can help.
- retiring soon? you need help.

Those are just general ideas, please feel free to be creative.

brand colors:
#00b585
#00b185
#000000
#ffffff
#6d6f75
#6d6f75
#6f7074
#021712
#052e24

```html
<!DOCTYPE html>
<html lang="en">
<head>
<meta charset="utf-8">
<title>Keystonery Billboard</title>
<link rel="stylesheet" href="https://fonts.googleapis.com/css2?family=Josefin+Sans:wght@400;600;700&display=swap">
<style>
  :root {
    --brand-green: #2bb38f;
    --accent-green: #00b185;
    --bubble-white: #f4f4f2;
    --text-gray: #6d6f75;
    --deep-ink: #052e24;
    --page-bg: #eef1f0;
  }
  * { margin: 0; padding: 0; box-sizing: border-box; }
  html, body {
    width: 1200px;
    height: 800px;
    overflow: hidden;
    background: var(--page-bg);
  }
  body {
    position: relative;
    font-family: "Josefin Sans", sans-serif;
  }
  .billboard {
    position: absolute;
    left: 20px;
    top: 101px;
    width: 1160px;
    height: 598px;
    background: var(--brand-green);
    overflow: hidden;
  }
  .speech-bubble {
    position: absolute;
    left: 0;
    top: 0;
    width: 1160px;
    height: 598px;
  }
  .headline {
    position: absolute;
    left: 217px;
    top: 134px;
    font-weight: 700;
    font-size: 76px;
    line-height: 82px;
    letter-spacing: 1px;
    color: var(--text-gray);
    text-transform: uppercase;
  }
  .offer {
    position: absolute;
    left: 214px;
    top: 305px;
    font-weight: 600;
    font-size: 38px;
    letter-spacing: 0.5px;
    color: var(--accent-green);
    text-transform: uppercase;
  }
  .phone {
    position: absolute;
    left: 212px;
    top: 343px;
    font-weight: 600;
    font-size: 62px;
    color: var(--text-gray);
  }
  .brand-name {
    position: absolute;
    left: 48px;
    top: 466px;
    display: flex;
    align-items: center;
    gap: 10px;
    font-weight: 700;
    font-size: 28px;
    color: var(--bubble-white);
  }
  .brand-name .brand-square {
    width: 16px;
    height: 16px;
    background: var(--bubble-white);
  }
  .service-note {
    position: absolute;
    left: 423px;
    top: 492px;
    font-weight: 400;
    font-size: 34px;
    letter-spacing: 1.5px;
    color: var(--deep-ink);
  }
</style>
</head>
<body>
  <main class="billboard">
    <svg class="speech-bubble" viewBox="0 0 1160 598" aria-hidden="true">
      <path fill="#000" opacity="0.12" transform="translate(6 8)"
        d="M259 57 H882 A150 150 0 0 1 1032 207 V287 A150 150 0 0 1 882 437 H420 C370 470 320 530 255 551 C285 510 290 470 280 437 H259 A150 150 0 0 1 109 287 V207 A150 150 0 0 1 259 57 Z"/>
      <path fill="var(--bubble-white)"
        d="M259 57 H882 A150 150 0 0 1 1032 207 V287 A150 150 0 0 1 882 437 H420 C370 470 320 530 255 551 C285 510 290 470 280 437 H259 A150 150 0 0 1 109 287 V207 A150 150 0 0 1 259 57 Z"/>
    </svg>

    <h1 class="headline">Need Investment<br>Advice?</h1>
    <p class="offer">Free Consultation</p>
    <p class="phone">302-418-2907</p>

    <div class="brand-name"><span class="brand-square"></span>Keystonery</div>

    <p class="service-note">serving the area since 1980</p>
  </main>
</body>
</html>
```